Hollow Marigold Distillery

I need a label designed for my small distillery. I’d like it to have a rose, and the name hollow marigold in script writing. I need the graphic to fit a standard gin bottle and I’ll need to be able to edit it depending on alcohol, warning and descriptions. I want it to look elegant and attractive, but slightly daring too. It’s a 700ml oslo bottle
Target Market(s)
Bespoke gin and vodka drinkers
Industry/Entity Type
Beverage
Font styles to use
Script
Other font styles liked:
- Something easy to read
Requirements
Must have
- Room for me to add and remove text depending on the drink
Nice to have
- Hollow marigold in script, slight colour on the rose and black writing

```html
<!DOCTYPE html>
<html lang="en">
<head>
<meta charset="utf-8">
<title>Hollow Marigold Rose Gin Labels</title>
<link rel="stylesheet" href="https://fonts.googleapis.com/css2?family=Great+Vibes&family=Yellowtail&family=Libre+Caslon+Text&family=Oswald:wght@500&display=swap">
<style>
  :root {
    --page: #ffffff;
    --label: #efefef;
    --frame: #c98a84;
    --ink: #111111;
    --band-deep: #b35a55;
    --band-light: #e3aaa3;
    --band-text: #f7e8e5;
    --pill-deep: #e2a098;
    --pill-light: #f6d9d4;
    --pill-text: #3b2b2b;
    --rose-line: #d9a09a;
    --rose-soft: #f7e4e2;
    --wash: #f2c9c5;
  }
  * { margin: 0; padding: 0; box-sizing: border-box; }
  html, body { width: 1200px; height: 1200px; overflow: hidden; background: var(--page); }
  .canvas { position: relative; width: 1200px; height: 1200px; }

  .label {
    position: absolute; top: 280px; width: 480px; height: 640px;
    background: var(--label);
  }
  .label--classic { left: 80px; }
  .label--modern { left: 640px; }

  .label__frame {
    position: absolute; inset: 14px;
    border: 2px solid var(--frame);
  }
  .label__wash {
    position: absolute; left: 16px; top: 30px; width: 170px; height: 560px;
    background: linear-gradient(90deg, var(--wash) 0%, rgba(242,201,197,0.35) 55%, rgba(242,201,197,0) 100%);
    opacity: 0.8;
  }

  .label__name {
    position: absolute; left: 0; right: 0; top: 90px;
    text-align: center; color: var(--ink); line-height: 1;
  }
  .label--classic .label__name {
    font-family: "Great Vibes", cursive; font-size: 84px; line-height: 92px;
  }
  .label--modern .label__name {
    font-family: "Yellowtail", cursive; font-size: 88px; line-height: 100px;
  }

  .label__rose {
    position: absolute; left: 70px; top: 320px; width: 350px; height: 170px;
    border-radius: 50%;
    background: radial-gradient(ellipse at 60% 50%, var(--rose-line) 0%, var(--rose-soft) 55%, rgba(247,228,226,0) 75%);
  }

  .label__band {
    position: absolute; left: 16px; right: 16px; top: 500px; height: 52px;
    background: linear-gradient(90deg, var(--band-deep) 0%, var(--band-deep) 45%, var(--band-light) 100%);
    display: flex; align-items: center; justify-content: center;
    font-family: "Libre Caslon Text", serif; font-size: 28px; letter-spacing: 1px;
    color: var(--band-text);
  }
  .label__pill {
    position: absolute; left: 235px; right: 16px; top: 490px; height: 58px;
    border-radius: 29px 0 0 29px;
    background: linear-gradient(90deg, var(--pill-deep) 0%, var(--pill-light) 100%);
    display: flex; align-items: center; justify-content: center;
    font-family: "Libre Caslon Text", serif; font-size: 28px; letter-spacing: 1px;
    color: var(--pill-text);
  }

  .label__spec {
    position: absolute; top: 572px;
    font-family: "Oswald", sans-serif; font-weight: 500; font-size: 20px;
    color: var(--ink); white-space: nowrap;
  }
  .label--classic .label__spec { left: 0; right: 0; text-align: center; }
  .label--modern .label__spec { left: 235px; right: 16px; text-align: center; top: 562px; }
  .label__divider { display: inline-block; margin: 0 8px; }
</style>
</head>
<body>
<main class="canvas">

  <section class="label label--classic">
    <div class="label__wash" role="img" aria-label="Soft pink watercolour wash"></div>
    <div class="label__frame"></div>
    <h1 class="label__name">Hollow<br>Marigold</h1>
    <div class="label__rose" role="img" aria-label="Line illustration of roses and blossoms in rose gold"></div>
    <div class="label__band">ROSE GIN</div>
    <p class="label__spec">40% ABV<span class="label__divider">|</span>700 ML</p>
  </section>

  <section class="label label--modern">
    <div class="label__frame"></div>
    <h1 class="label__name">Hollow<br>Marigold</h1>
    <div class="label__rose" role="img" aria-label="Line illustration of roses and blossoms in rose gold"></div>
    <div class="label__pill">ROSE GIN</div>
    <p class="label__spec">40% ABV<span class="label__divider">|</span>700 ML</p>
  </section>

</main>
</body>
</html>
```